RW Framewell Inc Business cards

We need business cards using our existing logo but slightly modified. Right now the logo says RW Loadbearing Masonry. We want to keep the RW part of the design, but replace the Structural Concrete portion with "FRAMEWELL". Please see the attached file.
Ideally this would be a blank template so we can add Different Names, titles, and phone numbers later.
On the one side we want only the logo and on the other side the detail. I'm attaching an example for you to see.
Please reach out with any other questions. Our address and other details will be given out once we find a design we like.

Target Market(s)

Construction Industry

```html
<!DOCTYPE html>
<html lang="en">
<head>
<meta charset="utf-8">
<title>RW Framewell Inc — Business Cards</title>
<link href="https://fonts.googleapis.com/css2?family=Montserrat:wght@600&family=Roboto:wght@400;500&display=swap" rel="stylesheet">
<style>
  :root {
    --brand-blue: #2e5f9f;
    --paper-white: #f3f3f1;
    --accent-grey: #6e6e6e;
    --backdrop: #e4e7ec;
    --text-light: #ffffff;
    --text-soft: #dfe7f3;
  }
  * { box-sizing: border-box; margin: 0; padding: 0; }
  html, body {
    width: 1200px; height: 852px; overflow: hidden;
    background: var(--backdrop);
  }
  .canvas { position: relative; width: 1200px; height: 852px; }

  .card {
    position: absolute;
    width: 525px; height: 300px;
    border-radius: 22px;
    overflow: hidden;
    box-shadow: 0 6px 18px rgba(0,0,0,0.18);
  }
  .card--front {
    left: 90px; top: 110px;
    background: var(--brand-blue);
    display: flex; align-items: center; justify-content: center;
  }
  .card--back { left: 585px; top: 440px; background: var(--brand-blue); }

  .wordmark {
    font-family: "Montserrat", sans-serif;
    font-weight: 600;
    text-align: center;
    line-height: 1;
  }
  .wordmark__initials { display: block; font-size: 76px; letter-spacing: 2px; }
  .wordmark__name { display: block; font-size: 24px; letter-spacing: 7px; margin-top: 10px; }
  .wordmark--light { color: var(--text-light); }
  .wordmark--blue { color: var(--brand-blue); }

  .back-shapes { position: absolute; inset: 0; }

  .back-logo {
    position: absolute; left: 40px; top: 92px; width: 230px;
  }
  .back-logo .wordmark__initials { font-size: 64px; }
  .back-logo .wordmark__name { font-size: 20px; letter-spacing: 6px; }

  .details {
    position: absolute; left: 318px; top: 52px; right: 18px;
    font-family: "Roboto", sans-serif;
    color: var(--text-light);
  }
  .details__name { font-size: 19px; font-weight: 500; }
  .details__title { font-size: 12px; color: var(--text-soft); margin-top: 3px; }
  .contact { list-style: none; margin-top: 20px; }
  .contact__item {
    display: flex; align-items: flex-start; gap: 8px;
    font-size: 11.5px; line-height: 1.35; margin-bottom: 7px;
  }
  .contact__icon { width: 12px; height: 12px; flex: none; margin-top: 1px; fill: var(--text-light); }
</style>
</head>
<body>
<main class="canvas">

  <section class="card card--front" aria-label="Card front">
    <div class="wordmark wordmark--light">
      <span class="wordmark__initials">RW</span>
      <span class="wordmark__name">FRAMEWELL</span>
    </div>
  </section>

  <section class="card card--back" aria-label="Card back">
    <svg class="back-shapes" viewBox="0 0 525 300" preserveAspectRatio="none" aria-hidden="true">
      <path d="M0 0 H238 C318 60 330 190 300 300 H0 Z" fill="var(--accent-grey)"/>
      <path d="M0 0 H222 C300 60 312 190 283 300 H0 Z" fill="var(--paper-white)"/>
    </svg>

    <div class="back-logo wordmark wordmark--blue">
      <span class="wordmark__initials">RW</span>
      <span class="wordmark__name">FRAMEWELL</span>
    </div>

    <div class="details">
      <p class="details__name">Mark Ellison</p>
      <p class="details__title">Managing Director</p>
      <ul class="contact">
        <li class="contact__item">
          <svg class="contact__icon" viewBox="0 0 24 24"><path d="M6.6 10.8a15.1 15.1 0 0 0 6.6 6.6l2.2-2.2c.3-.3.7-.4 1-.2 1.1.4 2.3.6 3.6.6.6 0 1 .4 1 1V20c0 .6-.4 1-1 1A17 17 0 0 1 3 4c0-.6.4-1 1-1h3.5c.6 0 1 .4 1 1 0 1.3.2 2.5.6 3.6.1.3 0 .7-.2 1z"/></svg>
          <span>828-555-0142</span>
        </li>
        <li class="contact__item">
          <svg class="contact__icon" viewBox="0 0 24 24"><path d="M2 5h20v14H2z M4 7v.5l8 5 8-5V7z" fill-rule="evenodd"/></svg>
          <span>mark@framewell.example</span>
        </li>
        <li class="contact__item">
          <svg class="contact__icon" viewBox="0 0 24 24"><circle cx="12" cy="12" r="10" fill="none" stroke="#fff" stroke-width="2"/><path d="M2 12h20M12 2c3 3 3 17 0 20M12 2c-3 3-3 17 0 20" fill="none" stroke="#fff" stroke-width="1.6"/></svg>
          <span>www.framewell.example</span>
        </li>
        <li class="contact__item">
          <svg class="contact__icon" viewBox="0 0 24 24"><path d="M12 2a7 7 0 0 0-7 7c0 5 7 13 7 13s7-8 7-13a7 7 0 0 0-7-7zm0 9.5A2.5 2.5 0 1 1 12 6.5a2.5 2.5 0 0 1 0 5z"/></svg>
          <span>58 Beamline Rd., Oakridge,<br>California, US 950214</span>
        </li>
      </ul>
    </div>
  </section>

</main>
</body>
</html>
```